Family business needs stationery redesign with new logo

Family owned company, established in 1987 wanting a brand 'refresh'. We are an electrical, refrigeration and construction company based in the Barkly Region Northern Territory, Australia. We have a new logo we would like to use which is uploaded along with our current letterhead and email signature. We are also dropping the word 'contractors' so please do not include this on any designs. Please note also, the 'orange' color used in our logo and designs should be Northern Territory red ochre which is as follows:

RGB (Hex): #C75B12
PantoneĀ® 159 C
CMYK: 1 / 74 / 100 / 7

We are needing our stationery redesigned using our new logo. Please include letterheads, business cards, envelopes, and email signatures.

We currently use our business letterheads for quotations, invoices, letters, HR matters, and internal memos.

We also need a separate simplified letterhead for internal paperwork such as employee leave forms, meeting agendas, and meeting minutes etc.

Reason: Needing more submissions of full package designs. We are wanting all our stationery, including business cards, letterheads, email signatures, envelopes, etc to be cohesive. We also require ALL the information, as supplied on our template letterhead, to be included on the new letterhead designs. including electrical license no.etc Thank you, R&W

Reason: needing more time as work has got in the way of looking over designs. A lot of designs not meeting the brief/criteria.

Industry/Entity Type

Business

Colors
0355a3
f37122

Requirements
Must have
• The 'orange' color used in the designs should be Northern Territory red ochre which is as follows:
• RGB (Hex): #C75B12
• PantoneĀ® 159 C
• CMYK: 1 / 74 / 100 / 7
• ***MUST INCLUDE ALL INFORMATION THAT IS ON OUR CURRENT LETTERHEAD***
Should not have
• Please do not include the word 'contractors'

```html
<!DOCTYPE html>
<html lang="en">
<head>
<meta charset="utf-8">
<title>R&amp;W Business Card</title>
<link href="https://fonts.googleapis.com/css2?family=Arimo:wght@400;700&display=swap" rel="stylesheet">
<style>
  :root {
    --page-bg: #e9eaee;
    --card-bg: #f7f8fa;
    --navy: #0f1c4d;
    --navy-deep: #08102f;
    --ochre: #c75b12;
    --ink: #2b2f3a;
    --name-blue: #1d2d5c;
    --mark-white: #e9ecf2;
  }
  * { margin: 0; padding: 0; box-sizing: border-box; }
  html, body {
    width: 1200px; height: 969px; overflow: hidden;
    background: var(--page-bg);
    font-family: "Arimo", Arial, sans-serif;
  }
  .business-card {
    position: absolute;
    left: 100px; top: 200px;
    width: 1000px; height: 568px;
    border-radius: 22px;
    background: var(--card-bg);
    overflow: hidden;
    box-shadow: 0 14px 40px rgba(20, 28, 60, 0.18);
  }
  .card-art { position: absolute; inset: 0; }
  .contact-block {
    position: absolute; left: 58px; top: 110px;
    color: var(--ink);
  }
  .person-name {
    font-weight: 700; font-size: 32px; letter-spacing: 0.5px;
    color: var(--name-blue);
  }
  .person-title {
    margin-top: 8px; font-size: 24px; color: var(--ochre);
  }
  .person-email { margin-top: 8px; font-size: 24px; }
  .contact-lines { margin-top: 34px; list-style: none; }
  .contact-lines li {
    display: flex; align-items: center; gap: 14px;
    font-size: 24px; height: 38px;
  }
  .contact-icon { width: 24px; height: 24px; fill: var(--name-blue); }
  .postal-address {
    margin-top: 28px; font-size: 24px; line-height: 38px; font-style: normal;
  }
  .brand-name {
    position: absolute; left: 521px; top: 222px; width: 410px;
    text-align: center;
    font-weight: 700; font-size: 128px; line-height: 1;
    color: var(--mark-white);
  }
</style>
</head>
<body>
  <div class="business-card">
    <svg class="card-art" width="1000" height="568" viewBox="0 0 1000 568" aria-hidden="true">
      <defs>
        <linearGradient id="navyPanel" x1="0" y1="0" x2="1" y2="1">
          <stop offset="0" stop-color="#1a2a66"/>
          <stop offset="0.55" stop-color="#0f1c4d"/>
          <stop offset="1" stop-color="#08102f"/>
        </linearGradient>
      </defs>
      <path d="M748,0 C520,40 421,170 421,290 C421,410 520,530 760,568 L1000,568 L1000,0 Z" fill="url(#navyPanel)"/>
      <path d="M790,0 C570,45 440,170 440,290 C440,410 560,525 800,568" fill="none" stroke="var(--ochre)" stroke-width="4"/>
    </svg>

    <div class="contact-block">
      <div class="person-name">DANIEL HART</div>
      <div class="person-title">CEO/Founder</div>
      <div class="person-email">hello@rwgroup.com</div>
      <ul class="contact-lines">
        <li>
          <svg class="contact-icon" viewBox="0 0 24 24"><path d="M6.6 10.8a15.1 15.1 0 0 0 6.6 6.6l2.2-2.2a1 1 0 0 1 1-.25 11.4 11.4 0 0 0 3.6.57 1 1 0 0 1 1 1V20a1 1 0 0 1-1 1A17 17 0 0 1 3 4a1 1 0 0 1 1-1h3.5a1 1 0 0 1 1 1c0 1.25.2 2.45.57 3.57a1 1 0 0 1-.25 1z"/></svg>
          <span>741 205 3896</span>
        </li>
        <li>
          <svg class="contact-icon" viewBox="0 0 24 24"><path d="M6 2h12v5H6z"/><path d="M3 8h18a1 1 0 0 1 1 1v8h-4v-3H6v3H2V9a1 1 0 0 1 1-1z"/><path d="M7 15h10v7H7z"/></svg>
          <span>563 812 4097</span>
        </li>
        <li>
          <svg class="contact-icon" viewBox="0 0 24 24"><circle cx="12" cy="12" r="10"/><path d="M12 2c3 3 3 17 0 20M12 2c-3 3-3 17 0 20M2 12h20" stroke="#f7f8fa" stroke-width="1.5" fill="none"/></svg>
          <span>www.rwgroup.com</span>
        </li>
      </ul>
      <address class="postal-address">
        412 Ridgeway Court<br>
        Tennant Creek, NT 0860
      </address>
    </div>

    <div class="brand-name">R&amp;W</div>
  </div>
</body>
</html>
```